Redesign of business card for Cedar Ridge Mechanical

We are looking for a new design for our business cards for Cedar Ridge Mechanical. We are a plumbing & HVAC construction company, operating on the West Coast of Canada and USA. Logo attached.
Industry/Entity Type
Construction - Plumbing & HVAC
Contact Information for Business Card
Name, address, phone numbers, email, website address
Look and feel
Each slider illustrates characteristics of the customer's brand and the style your logo design should communicate.

```html
<!DOCTYPE html>
<html lang="en">
<head>
<meta charset="utf-8">
<title>Cedar Ridge Mechanical – Business Card</title>
<link href="https://fonts.googleapis.com/css2?family=Roboto:wght@400;700&family=Roboto+Condensed:wght@700&display=swap" rel="stylesheet">
<style>
  :root {
    --bg: #9a9a9a;
    --paper: #ffffff;
    --ink: #1c1c1c;
    --muted: #8a8a8a;
    --dark-card: #2b2b2b;
    --on-dark: #ffffff;
  }
  html, body {
    margin: 0;
    padding: 0;
    overflow: hidden;
  }
  .canvas {
    position: relative;
    width: 1200px;
    height: 1050px;
    background: var(--bg);
    overflow: hidden;
    font-family: "Roboto", Arial, sans-serif;
  }
  .card {
    position: absolute;
    border-radius: 18px;
    box-shadow: 0 6px 18px rgba(0,0,0,0.25);
    box-sizing: border-box;
  }
  /* Front: portrait, white */
  .card-front {
    left: 110px;
    top: 190px;
    width: 380px;
    height: 665px;
    background: var(--paper);
    color: var(--ink);
    display: flex;
    flex-direction: column;
    align-items: center;
    padding-top: 70px;
    text-align: center;
  }
  .wordmark {
    display: flex;
    align-items: center;
    gap: 10px;
    font-family: "Roboto Condensed", Arial, sans-serif;
    font-weight: 700;
    letter-spacing: 0.06em;
    text-transform: uppercase;
  }
  .wordmark .mark-square {
    border: 4px solid currentColor;
    box-sizing: border-box;
  }
  .card-front .wordmark { font-size: 17px; flex-direction: column; gap: 12px; }
  .card-front .mark-square { width: 46px; height: 46px; }
  .person-name {
    margin-top: 48px;
    font-size: 27px;
    font-weight: 700;
  }
  .person-title {
    margin-top: 2px;
    font-size: 20px;
    color: var(--muted);
  }
  .icon-row {
    margin-top: 20px;
    display: flex;
    align-items: center;
    gap: 6px;
  }
  .icon-row .rule { width: 22px; height: 1.5px; background: var(--ink); }
  .icon-row svg { width: 22px; height: 22px; display: block; }
  .contact-list {
    margin-top: 22px;
    font-size: 18px;
    line-height: 1.35;
  }
  .divider {
    margin: 28px 0 24px;
    width: 110px;
    height: 1.5px;
    background: var(--ink);
  }
  .address {
    font-size: 18px;
    line-height: 1.35;
  }
  /* Back: landscape, dark */
  .card-back {
    left: 560px;
    top: 400px;
    width: 560px;
    height: 320px;
    background: var(--dark-card);
    color: var(--on-dark);
    display: flex;
    align-items: center;
    justify-content: center;
  }
  .card-back .wordmark { font-size: 30px; gap: 16px; }
  .card-back .mark-square { width: 40px; height: 40px; border-width: 5px; }
</style>
</head>
<body>
<main class="canvas">
  <section class="card card-front" aria-label="Business card front">
    <div class="wordmark">
      <span class="mark-square"></span>
      <span class="wordmark-name">Cedar Ridge Mechanical</span>
    </div>
    <div class="person-name">Daniel Hayes</div>
    <div class="person-title">President</div>
    <div class="icon-row">
      <span class="rule"></span>
      <svg viewBox="0 0 24 24" aria-label="Phone">
        <circle cx="12" cy="12" r="11" fill="#1c1c1c"/>
        <path d="M8.5 6.5l2 2-1.2 1.6c.8 1.7 2 2.9 3.6 3.6l1.6-1.2 2 2-1.3 1.8c-4.2-.6-7.9-4.3-8.5-8.5z" fill="#fff"/>
      </svg>
      <svg viewBox="0 0 24 24" aria-label="Email">
        <circle cx="12" cy="12" r="11" fill="#1c1c1c"/>
        <rect x="6.5" y="8" width="11" height="8" fill="#fff"/>
        <path d="M6.5 8l5.5 4.5L17.5 8" fill="none" stroke="#1c1c1c" stroke-width="1.2"/>
      </svg>
      <svg viewBox="0 0 24 24" aria-label="Website">
        <circle cx="12" cy="12" r="11" fill="#1c1c1c"/>
        <circle cx="12" cy="12" r="5.5" fill="none" stroke="#fff" stroke-width="1.3"/>
        <path d="M6.5 12h11M12 6.5c-2.2 3-2.2 8 0 11M12 6.5c2.2 3 2.2 8 0 11" fill="none" stroke="#fff" stroke-width="1.1"/>
      </svg>
      <span class="rule"></span>
    </div>
    <div class="contact-list">
      <div>(604) 555-0187</div>
      <div>name@cedarridgemechanical.com</div>
      <div>www.cedarridgemechanical.com</div>
    </div>
    <div class="divider"></div>
    <div class="address">
      <div>2170 Harbor View Road</div>
      <div>Bellingham, WA 98225</div>
    </div>
  </section>

  <section class="card card-back" aria-label="Business card back">
    <div class="wordmark">
      <span class="mark-square"></span>
      <span class="wordmark-name">Cedar Ridge Mechanical</span>
    </div>
  </section>
</main>
</body>
</html>
```